Caldrift - Where every box finds its place!

Hello,
I'd like to update, re-vamp, and re-tool this current power point presentation with slightly more professional appearance as well as more accurately reflect the website -caldrift.com- color scheme and sleek design scheme. Please see attached.
We at Caldrift pride ourselves on seeking to rework an archaic business into something progressive, cost effective, more reliable, and easily accessible in todays fast growing market that has only gotten more expensive, more costly and less indirect over the last couple years.

Target Market(s)

New updated and hassle free moving opportunities no matter how large or how small in a market that begs for a change

Industry/Entity Type

Logistics/Moving

Requirements
Must have
• The current color scheme from the -caldrift.com- website as well as the inclusion of the current data on the sample power point presentation provided but with updated graphics

```html
<!DOCTYPE html>
<html lang="en">
<head>
<meta charset="utf-8">
<title>Caldrift - Where every box finds its place!</title>
<link href="https://fonts.googleapis.com/css2?family=Montserrat:wght@400;500;600;700;800&display=swap" rel="stylesheet">
<style>
:root{
  --page:#e8e9eb;
  --slide:#ffffff;
  --blue:#1c57c8;
  --blue-dark:#123f98;
  --gold:#d8b64c;
  --ink:#1b1d22;
  --muted:#5b5f68;
  --photo-a:#b8a48a;
  --photo-b:#d9cdbd;
}
*{box-sizing:border-box;margin:0;padding:0}
html,body{width:1200px;height:4088px;overflow:hidden;background:var(--page);font-family:"Montserrat",Arial,sans-serif;color:var(--ink)}
.deck{position:relative;width:1200px;height:4088px}
.slide{position:absolute;left:40px;width:1120px;height:630px;background:var(--slide);overflow:hidden;box-shadow:0 2px 8px rgba(0,0,0,.08)}
.brand{position:absolute;display:flex;align-items:center;gap:12px;font-weight:700;font-size:34px;color:var(--blue);letter-spacing:.5px}
.brand-mark{width:26px;height:26px;background:var(--blue)}
.site{position:absolute;font-size:11px;font-weight:600;letter-spacing:3px;color:var(--blue)}
.heading{position:absolute;font-weight:800;color:var(--ink);letter-spacing:1px;text-transform:uppercase}
.photo{position:absolute;background:linear-gradient(135deg,var(--photo-a),var(--photo-b))}

/* slide 1 */
.cover .brand{left:0;right:0;justify-content:center;top:30px}
.cover .heading{left:0;right:0;text-align:center;top:96px;font-size:22px;letter-spacing:2px}
.cover svg{position:absolute;left:0;top:140px}
.cover .site{left:0;right:0;text-align:center;top:602px}

/* slide 2 */
.about .brand{left:40px;top:30px}
.about .heading{right:50px;top:34px;font-size:34px}
.about .hex{position:absolute;left:50px;top:100px}
.about-copy{position:absolute;left:450px;right:50px;top:150px;text-align:right;font-size:15.5px;line-height:1.7;font-weight:500;color:var(--ink)}
.about-copy p+p{margin-top:20px}
.about .site{left:50px;top:596px}

/* slide 3 */
.vision .brand{left:40px;top:30px}
.vision .heading{right:50px;top:34px;font-size:30px}
.vision .lead{position:absolute;right:50px;top:90px;width:560px;text-align:right;font-size:17px;font-weight:700;color:var(--blue);line-height:1.4}
.pillars{position:absolute;left:40px;top:230px;width:1040px;height:300px}
.pillar{position:absolute;top:0;height:300px;color:#fff;text-align:center;padding:34px 40px 0}
.pillar.p1{left:0;width:345px;background:var(--blue);clip-path:polygon(0 0,100% 12%,100% 100%,0 100%)}
.pillar.p2{left:347px;width:346px;top:10px;background:var(--gold);clip-path:polygon(0 0,100% 0,100% 100%,0 100%)}
.pillar.p3{left:695px;width:345px;background:var(--blue);clip-path:polygon(0 12%,100% 0,100% 100%,0 100%)}
.pillar svg{display:block;margin:0 auto 10px}
.pillar h3{font-size:16px;font-weight:700;margin-bottom:8px}
.pillar .bold{font-size:12px;font-weight:700;line-height:1.4;margin-bottom:8px}
.pillar .small{font-size:10px;line-height:1.5;font-weight:500;opacity:.92}
.vision .site{left:50px;top:596px}

/* slide 4 */
.problems .brand{left:40px;top:30px}
.problems .heading{right:50px;top:34px;font-size:30px}
.problems .truck{left:50px;top:170px;width:520px;height:300px;background:linear-gradient(160deg,#dfe3e8,#aeb5bd);border-radius:6px}
.issue{position:absolute;right:50px;width:440px;display:flex;align-items:center;justify-content:flex-end;gap:20px}
.issue-text{text-align:right}
.issue-text h4{font-size:18px;font-weight:800;margin-bottom:4px}
.issue-text p{font-size:10.5px;line-height:1.5;color:var(--muted);font-weight:500}
.problems .site{left:50px;top:596px}

/* slide 5 */
.done .brand{left:40px;top:30px}
.done .heading{right:50px;top:34px;font-size:30px;text-align:right;line-height:1.2}
.done .crowd{left:310px;top:150px;width:500px;height:420px;border-radius:50% 50% 46% 54%/ 55% 50% 50% 45%;background:radial-gradient(ellipse at 50% 45%,#6c6a68,#c9c7c4 70%,#fff 100%)}
.done svg.lines{position:absolute;left:0;top:0}
.goal{position:absolute;font-size:13px;font-weight:700;color:var(--ink);line-height:1.3}
.done .site{left:50px;top:596px}

/* slide 6 */
.solution .brand{left:40px;top:30px}
.solution .heading{right:50px;top:34px;font-size:30px}
.solution .sub{position:absolute;right:50px;top:76px;font-size:13px;font-weight:700;letter-spacing:1px}
.solution .tag{position:absolute;right:50px;top:96px;font-size:14px;font-weight:700;color:var(--blue);letter-spacing:.5px}
.solution .rule{position:absolute;left:0;right:0;top:120px;height:2px;background:var(--blue);opacity:.85}
.offer{position:absolute;width:190px;text-align:center}
.offer svg{display:block;margin:0 auto 12px}
.offer h4{font-size:13px;font-weight:700;margin-bottom:6px}
.offer p{font-size:10px;line-height:1.5;color:var(--muted);font-weight:500}
.solution .site{left:50px;top:596px}
</style>
</head>
<body>
<div class="deck">

<!-- Cover -->
<section class="slide cover" style="top:44px">
  <div class="brand"><span class="brand-mark"></span>Caldrift</div>
  <h1 class="heading">Moving for the next generation</h1>
  <svg width="1120" height="450" viewBox="0 0 1120 450">
    <rect x="0" y="0" width="1120" height="450" fill="url(#coverPhoto)" role="img" aria-label="Movers carrying boxes and a wrapped sofa out of a moving truck"/>
    <defs><linearGradient id="coverPhoto" x1="0" y1="0" x2="1" y2="1"><stop offset="0" stop-color="#8d7d6a"/><stop offset=".5" stop-color="#cdb99d"/><stop offset="1" stop-color="#e6ddd0"/></linearGradient></defs>
    <polygon points="0,0 1120,0 1120,20 560,90 0,20" fill="#fff"/>
    <polyline points="0,20 560,90 1120,20" fill="none" stroke="#1c57c8" stroke-width="12"/>
  </svg>
  <div class="site">WWW.CALDRIFT.COM</div>
</section>

<!-- About -->
<section class="slide about" style="top:718px">
  <div class="brand"><span class="brand-mark"></span>Caldrift</div>
  <h2 class="heading">About us</h2>
  <svg class="hex" width="360" height="440" viewBox="0 0 360 440">
    <polygon points="10,300 10,430 150,430" fill="#1c57c8"/>
    <polygon points="180,10 340,100 340,300 180,390 20,300 20,100" fill="url(#aboutPhoto)" role="img" aria-label="Family unpacking moving boxes in a new home"/>
    <defs><linearGradient id="aboutPhoto" x1="0" y1="0" x2="1" y2="1"><stop offset="0" stop-color="#c7b29a"/><stop offset="1" stop-color="#efe7dc"/></linearGradient></defs>
    <polygon points="180,10 340,100 340,300 180,390 20,300 20,100" fill="none" stroke="#1c57c8" stroke-width="6"/>
  </svg>
  <div class="about-copy">
    <p>Caldrift is the next logical evolution in professional moving. Professional moving clients have battled soaring prices, acute capacity problems and deteriorating service levels.</p>
    <p>Caldrift was founded by lifelong moving professionals who have developed the answer to better moving services. Poised as THE industry disruptor, we deliver faster, offer guaranteed prices and even offer no credit check financing options. We are a technology first organization using proprietary software to deliver moving's best service experience.</p>
  </div>
  <div class="site">WWW.CALDRIFT.COM</div>
</section>

<!-- Vision -->
<section class="slide vision" style="top:1392px">
  <div class="brand"><span class="brand-mark"></span>Caldrift</div>
  <h2 class="heading">Caldrift Vision</h2>
  <p class="lead">The traditional moving industry is broken, outdated, inefficient, and unable to change.</p>
  <div class="pillars">
    <div class="pillar p1">
      <svg width="40" height="40" viewBox="0 0 40 40" fill="none" stroke="#fff" stroke-width="2.4"><circle cx="20" cy="20" r="14"/><circle cx="20" cy="20" r="5"/><path d="M20 2v8M20 30v8M2 20h8M30 20h8"/></svg>
      <h3>Our Vision</h3>
      <p class="bold">Revolutionize an $86B industry by providing great value to everyone involved</p>
      <p class="small">Customers, consultants, movers, corporate clients and relocation partners all get better value with Caldrift than anywhere else.</p>
    </div>
    <div class="pillar p2">
      <svg width="40" height="40" viewBox="0 0 40 40" fill="none" stroke="#fff" stroke-width="2.4"><path d="M20 4l4 10h10l-8 7 3 11-9-6-9 6 3-11-8-7h10z"/></svg>
      <h3>Our Mission</h3>
      <p class="bold">Being a driving agent of an inefficient industry</p>
      <p class="small">Removing pain, unpredictability and unnecessary expense from every relocation through smarter planning, honest pricing and technology that works for customers and crews alike.</p>
    </div>
    <div class="pillar p3">
      <svg width="40" height="40" viewBox="0 0 40 40" fill="none" stroke="#fff" stroke-width="2.4"><path d="M8 36V6M8 6h22l-5 7 5 7H8"/></svg>
      <h3>Our Goal</h3>
      <p class="bold">Becoming the moving platform of choice</p>
      <p class="small">As Caldrift's reach grows, we serve the customer population with real-time price and operational improvements, more capacity and exceptional growth.</p>
    </div>
  </div>
  <div class="site">WWW.CALDRIFT.COM</div>
</section>

<!-- Problems -->
<section class="slide problems" style="top:2066px">
  <div class="brand"><span class="brand-mark"></span>Caldrift</div>
  <h2 class="heading">Moving's problems</h2>
  <div class="photo truck" role="img" aria-label="White box truck with company branding on the side"></div>
  <div class="issue" style="top:105px">
    <div class="issue-text"><h4>COST</h4><p>Moving costs have risen sharply over the last three years. Average prices are up more than 30% since 2019.</p></div>
    <svg width="56" height="56" viewBox="0 0 56 56"><rect x="10" y="10" width="36" height="36" transform="rotate(45 28 28)" fill="#1c57c8"/><text x="28" y="34" text-anchor="middle" font-family="Montserrat,sans-serif" font-weight="700" font-size="17" fill="#fff">$</text></svg>
  </div>
  <div class="issue" style="top:220px">
    <div class="issue-text"><h4>CAPACITY</h4><p>Long-haul driver shortages and limited equipment mean peak-season demand regularly outpaces available capacity.</p></div>
    <svg width="56" height="56" viewBox="0 0 56 56"><rect x="10" y="10" width="36" height="36" transform="rotate(45 28 28)" fill="#1c57c8"/><rect x="19" y="22" width="12" height="10" fill="none" stroke="#fff" stroke-width="2"/><path d="M31 25h4l3 3v4h-7" fill="none" stroke="#fff" stroke-width="2"/><circle cx="23" cy="34" r="2" fill="#fff"/><circle cx="34" cy="34" r="2" fill="#fff"/></svg>
  </div>
  <div class="issue" style="top:335px">
    <div class="issue-text"><h4>SERVICE</h4><p>Quality falls when crews are stretched thin, leading to damaged goods, missed windows and declining reviews.</p></div>
    <svg width="56" height="56" viewBox="0 0 56 56"><rect x="10" y="10" width="36" height="36" transform="rotate(45 28 28)" fill="#1c57c8"/><circle cx="28" cy="24" r="5" fill="none" stroke="#fff" stroke-width="2"/><path d="M19 37c2-6 16-6 18 0" fill="none" stroke="#fff" stroke-width="2"/></svg>
  </div>
  <div class="issue" style="top:450px">
    <div class="issue-text"><h4>TRANSPARENCY</h4><p>Too many hidden fees, vague estimates and middlemen leave customers confused and frustrated.</p></div>
    <svg width="56" height="56" viewBox="0 0 56 56"><rect x="10" y="10" width="36" height="36" transform="rotate(45 28 28)" fill="#1c57c8"/><circle cx="26" cy="26" r="6" fill="none" stroke="#fff" stroke-width="2"/><path d="M30 30l6 6" stroke="#fff" stroke-width="2.4"/></svg>
  </div>
  <div class="site">WWW.CALDRIFT.COM</div>
</section>

<!-- Accomplished -->
<section class="slide done" style="top:2740px">
  <div class="brand"><span class="brand-mark"></span>Caldrift</div>
  <h2 class="heading">What Caldrift has<br>accomplished</h2>
  <div class="photo crowd" role="img" aria-label="Aerial view of a crowd of people forming the shape of a rocket"></div>
  <svg class="lines" width="1120" height="630" viewBox="0 0 1120 630" fill="none" stroke="#1b1d22" stroke-width="1.2">
    <path d="M300 198 L420 250"/><circle cx="420" cy="250" r="3" fill="#1b1d22"/>
    <path d="M210 282 L400 300"/><circle cx="400" cy="300" r="3" fill="#1b1d22"/>
    <path d="M190 372 L400 360"/><circle cx="400" cy="360" r="3" fill="#1b1d22"/>
    <path d="M870 342 L720 340"/><circle cx="720" cy="340" r="3" fill="#1b1d22"/>
    <path d="M880 468 L700 420"/><circle cx="700" cy="420" r="3" fill="#1b1d22"/>
  </svg>
  <div class="goal" style="left:200px;top:166px;text-align:right;width:170px">Eliminate Capacity<br>Constraints</div>
  <div class="goal" style="left:100px;top:272px;text-align:right;width:105px">Reduce Costs</div>
  <div class="goal" style="left:60px;top:354px;text-align:right;width:125px">Improve Service<br>Levels</div>
  <div class="goal" style="left:880px;top:326px">Simplify the<br>Moving Process</div>
  <div class="goal" style="left:890px;top:456px">Break the Typical<br>Moving Mold</div>
  <div class="site">WWW.CALDRIFT.COM</div>
</section>

<!-- Solution -->
<section class="slide solution" style="top:3414px">
  <div class="brand"><span class="brand-mark"></span>Caldrift</div>
  <h2 class="heading">Solution</h2>
  <div class="sub">VALUE PROPOSITION</div>
  <div class="tag">BRINGING THE CUSTOMER EXPERIENCE TO THE 21ST CENTURY</div>
  <div class="rule"></div>

  <div class="offer" style="left:25px;top:300px">
    <svg width="100" height="100" viewBox="0 0 100 100"><rect x="18" y="18" width="64" height="64" transform="rotate(45 50 50)" fill="#1c57c8"/><path d="M36 62V44M46 62V36M56 62V48M66 62V40" stroke="#fff" stroke-width="4"/></svg>
    <h4>On-Demand Process</h4>
    <p>Caldrift automatically books verified movers, handling insurance, licensing and quality checks for you.</p>
  </div>
  <div class="offer" style="left:240px;top:190px">
    <svg width="100" height="100" viewBox="0 0 100 100"><rect x="18" y="18" width="64" height="64" transform="rotate(45 50 50)" fill="#1c57c8"/><rect x="35" y="40" width="30" height="21" fill="none" stroke="#fff" stroke-width="3"/><path d="M35 40l15 12 15-12" fill="none" stroke="#fff" stroke-width="3"/></svg>
    <h4>One Point of Contact</h4>
    <p>Today moves are split from broker to mover. Caldrift gives you a single dedicated contact from quote to delivery.</p>
  </div>
  <div class="offer" style="left:460px;top:300px">
    <svg width="100" height="100" viewBox="0 0 100 100"><rect x="18" y="18" width="64" height="64" transform="rotate(45 50 50)" fill="#1c57c8"/><rect x="34" y="38" width="32" height="24" rx="3" fill="none" stroke="#fff" stroke-width="3"/><path d="M34 46h32" stroke="#fff" stroke-width="3"/></svg>
    <h4>Book Now Pay Later</h4>
    <p>Moving is a major expense. Lock in your date today and pay in easy monthly installments later.</p>
  </div>
  <div class="offer" style="left:680px;top:190px">
    <svg width="100" height="100" viewBox="0 0 100 100"><rect x="18" y="18" width="64" height="64" transform="rotate(45 50 50)" fill="#1c57c8"/><path d="M50 66s-12-13-12-21a12 12 0 0 1 24 0c0 8-12 21-12 21z" fill="none" stroke="#fff" stroke-width="3"/><circle cx="50" cy="45" r="4" fill="#fff"/></svg>
    <h4>GPS Tracking</h4>
    <p>Follow your belongings in real time from pickup to drop-off, right from your phone.</p>
  </div>
  <div class="offer" style="left:900px;top:300px">
    <svg width="100" height="100" viewBox="0 0 100 100"><rect x="18" y="18" width="64" height="64" transform="rotate(45 50 50)" fill="#1c57c8"/><path d="M38 40h14l12 12-12 12-14-14z" fill="none" stroke="#fff" stroke-width="3"/><circle cx="44" cy="46" r="2.5" fill="#fff"/></svg>
    <h4>Simple Honest Pricing</h4>
    <p>Caldrift's pricing engine gives an upfront, all-in quote so the price you see is the price you pay.</p>
  </div>
  <div class="site">WWW.CALDRIFT.COM</div>
</section>

</div>
</body>
</html>
```